Zestora - Landing Page

Need a landing page for a journal app. The app is based on a retrospective board, where each journal entry is split into 3 sections: "What went well", "What Didn't Go Well" and "Things To Try".
The landing page should match the style of all modern web application landing pages. Think Brint, Tivalo, Mirvane. I've included screenshots of the app.
One feature that I want to highlight that is not ready yet, is an AI coach. It will offer insights based on the history of the user's journal entries
1 page

```html
<!DOCTYPE html>
<html lang="en">
<head>
<meta charset="utf-8">
<title>Zestora – Reflect, Grow, and Move Forward</title>
<link href="https://fonts.googleapis.com/css2?family=Figtree:wght@400;500;600;700;800&display=swap" rel="stylesheet">
<style>
:root{
  --ink:#1b1f2a;
  --text:#2d3340;
  --muted:#5a6170;
  --brand:#0b4ea8;
  --brand-deep:#0a3f8f;
  --band:#e8f0f8;
  --frame:#7eaad6;
  --side:#1f2937;
  --line:#d9dde3;
  --tool:#eef0f3;
  --white:#ffffff;
  --green:#22c55e;
  --lime:#a3e635;
}
*{box-sizing:border-box;margin:0;padding:0}
html,body{width:1200px;height:3713px;overflow:hidden}
body{font-family:"Figtree",Arial,sans-serif;color:var(--text);background:var(--white);position:relative}
.abs{position:absolute}
a{color:inherit;text-decoration:none}

/* nav */
.brand{font-weight:800;color:var(--ink);letter-spacing:.3px}
.nav-logo{left:131px;top:30px;font-size:32px}
.nav-link{top:32px;height:40px;line-height:40px;font-size:15px;color:var(--ink)}
.nav-home{left:416px;width:81px;background:var(--brand);color:#fff;border-radius:20px;text-align:center}
.btn{display:block;text-align:center;background:var(--brand);color:#fff;border-radius:22px;font-weight:500}
.nav-cta{left:938px;top:32px;width:129px;height:40px;line-height:40px;font-size:15px}

/* hero */
.hero-title{left:0;width:1200px;top:124px;text-align:center;font-size:40px;font-weight:400;color:var(--ink)}
.hero-sub{left:0;width:1200px;top:188px;text-align:center;font-size:16px;line-height:23px;color:var(--text)}
.hero-cta{left:498px;top:258px;width:202px;height:45px;line-height:45px;font-size:16px;border-radius:23px}

.band{left:0;width:1200px;background:var(--band)}

/* app screen */
.app-frame{left:140px;top:353px;width:920px;height:527px;border:10px solid var(--frame);border-radius:14px;background:#fff;overflow:hidden}
.app{position:absolute;left:0;top:0;width:900px;height:507px;background:#fff;transform-origin:0 0}
.app-side{position:absolute;left:0;top:0;width:38px;height:100%;background:var(--side)}
.side-logo{position:absolute;left:11px;top:10px;width:16px;height:14px;background:var(--lime);border-radius:2px}
.side-ico{position:absolute;left:14px;width:10px;height:9px;border:1.5px solid #cbd2dc;border-radius:2px}
.side-avatar{position:absolute;left:9px;bottom:10px;width:20px;height:20px;border-radius:50%;background:#cbd2dc}
.app-title{position:absolute;left:101px;top:14px;font-size:14px;font-weight:700;color:var(--ink)}
.app-date{position:absolute;left:106px;top:44px;font-size:9px;color:var(--ink);display:flex;align-items:center;gap:5px;white-space:nowrap}
.app-date svg{flex:none}
.app-pill{position:absolute;left:226px;top:41px;font-size:8px;color:#fff;background:#4b5563;border-radius:8px;padding:2px 9px;font-weight:600;white-space:nowrap}
.col{position:absolute;top:84px;width:226px;height:389px;border:1px solid var(--line);border-radius:2px;background:#fff}
.col-head{position:absolute;left:10px;top:11px;font-size:9px;color:var(--ink);display:flex;gap:7px;align-items:center;white-space:nowrap}
.col-tools{position:absolute;left:6px;top:40px;right:6px;height:34px;background:var(--tool);font-size:7px;color:var(--ink);padding:5px 9px;line-height:12px;letter-spacing:1px;white-space:nowrap;overflow:hidden}
.col-edit{position:absolute;left:14px;right:14px;top:84px;bottom:10px;border:1px solid var(--line)}
.col-edit i{display:block;height:4px;margin:7px 9px 0;background:#c6cbd3;border-radius:2px}

/* features */
.section-title{left:0;width:1200px;text-align:center;font-size:40px;font-weight:400;color:var(--ink)}
.rule{height:2px;background:var(--frame)}
.feature{top:1071px;width:230px;text-align:center}
.feature-icon{width:86px;height:86px;border-radius:50%;background:var(--brand);margin:0 auto;display:flex;align-items:center;justify-content:center}
.feature h3{margin-top:34px;font-size:16px;font-weight:600;color:var(--ink)}
.feature p{margin-top:14px;font-size:12.5px;line-height:16.5px;color:var(--text);padding:0 16px}

/* rows */
.shot{width:450px;height:281px;background:var(--brand);border-radius:12px;overflow:hidden}
.shot-screen{position:absolute;left:34px;top:22px;width:398px;height:232px;overflow:hidden;background:#fff}
.row-title{font-size:36px;line-height:42px;font-weight:400;color:var(--ink);width:440px}
.row-text{font-size:15px;line-height:21px;color:var(--text);width:420px}
.row-btn{width:113px;height:39px;line-height:39px;font-size:14px;border-radius:20px}

.list-card{position:absolute;left:84px;right:20px;border:1px solid var(--line);border-radius:3px;padding:10px 12px}
.list-card b{display:block;font-size:8px;color:var(--ink)}
.list-card i{display:block;height:3px;margin-top:5px;background:#c6cbd3;border-radius:2px}

/* testimonial */
.quote-text{left:200px;width:800px;top:2666px;text-align:center;font-size:19px;line-height:30px;color:var(--text);white-space:nowrap}
.arrow{width:50px;height:50px;border:2px solid var(--brand);border-radius:50%;display:flex;align-items:center;justify-content:center}
.author{left:0;width:1200px;top:2861px;text-align:center;font-size:17px;font-weight:600;color:var(--ink)}

/* cta */
.cta{left:0;top:2935px;width:1200px;height:423px;background:linear-gradient(120deg,#0a4cbf 0%,#0d57cc 50%,#1a6cd8 100%);overflow:hidden}
.cta-blob{position:absolute;width:200px;height:520px;border-radius:100px;background:rgba(255,255,255,.08);transform:rotate(45deg)}
.cta-title{left:0;width:1200px;top:90px;text-align:center;font-size:48px;font-weight:400;color:#fff}
.cta-text{left:0;width:1200px;top:173px;text-align:center;font-size:21px;line-height:35px;color:#fff}
.cta-btn{left:508px;top:285px;width:234px;height:52px;line-height:52px;background:#fff;color:var(--brand);border-radius:26px;font-size:18px;text-align:center}

/* footer */
.foot-logo{left:131px;top:3440px;font-size:42px}
.foot-col h4{font-size:19px;font-weight:500;color:var(--brand);margin-bottom:8px}
.foot-col a{display:block;font-size:14px;line-height:22.5px;color:var(--text)}
.social{display:flex;gap:8px}
.social span{width:26px;height:26px;border-radius:50%;border:1.5px solid var(--brand)}
.foot-rule{left:131px;top:3596px;width:939px;height:1px;background:#cfd5dd}
.legal{left:0;width:1200px;top:3641px;text-align:center;font-size:13px;color:var(--text)}
</style>
</head>
<body>

<!-- navigation -->
<header>
  <div class="abs brand nav-logo">Zestora</div>
  <a class="abs nav-link nav-home" href="#">Home</a>
  <a class="abs nav-link" style="left:512px" href="#">About Us</a>
  <a class="abs nav-link" style="left:608px" href="#">Features</a>
  <a class="abs nav-link" style="left:705px" href="#">Resources</a>
  <a class="abs nav-link" style="left:809px" href="#">Pricing</a>
  <svg class="abs" style="left:889px;top:42px" width="20" height="20" viewBox="0 0 20 20" fill="none" stroke="#1b1f2a" stroke-width="1.8"><circle cx="8" cy="8" r="6"/><path d="M12.5 12.5L18 18"/></svg>
  <a class="abs btn nav-cta" href="#">Get Started</a>
</header>

<!-- hero -->
<section>
  <h1 class="abs hero-title">Reflect, Grow, and Move Forward</h1>
  <p class="abs hero-sub">Your personal journal for mindful retrospectives. Track your progress with<br>structured entries that help you focus on what matters.</p>
  <a class="abs btn hero-cta" href="#">Get Started for Free</a>
</section>

<div class="abs band" style="top:617px;height:737px"></div>

<!-- product screen -->
<div class="abs app-frame">
  <div class="app">
    <div class="app-side">
      <div class="side-logo"></div>
      <div class="side-ico" style="top:46px"></div>
      <div class="side-ico" style="top:67px"></div>
      <div class="side-ico" style="top:88px"></div>
      <div class="side-avatar"></div>
    </div>
    <div class="app-title">Entry</div>
    <div class="app-date"><svg width="8" height="8" viewBox="0 0 8 8"><rect x=".5" y="1.5" width="7" height="6" fill="none" stroke="#1b1f2a"/><path d="M.5 3.5h7" stroke="#1b1f2a"/></svg>Wed Aug 21 2024 ⌄</div>
    <div class="app-pill">Default Journal</div>
    <div class="col" style="left:101px">
      <div class="col-head"><svg width="11" height="10" viewBox="0 0 11 10"><path d="M0 4h2v6H0zM3 4l3-4c1 0 1.5.7 1.2 2L7 4h3c.7 0 1 .6.9 1.2L10 9c-.2.6-.6 1-1.2 1H3z" fill="#2563eb"/></svg>What Went Well?</div>
      <div class="col-tools">Normal &nbsp;&nbsp;&nbsp;⇕ &nbsp;&nbsp;&nbsp;<b>B</b> <i>I</i> <u>U</u> <s>S</s> ”<br>☰ ☰ ⇤ ⇥ &nbsp;&nbsp;T</div>
      <div class="col-edit"></div>
    </div>
    <div class="col" style="left:357px">
      <div class="col-head"><svg width="11" height="10" viewBox="0 0 11 10"><path d="M5.5 0L11 10H0z" fill="#2563eb"/></svg>What Didn't Go Well?</div>
      <div class="col-tools">Normal &nbsp;&nbsp;&nbsp;⇕ &nbsp;&nbsp;&nbsp;<b>B</b> <i>I</i> <u>U</u> <s>S</s> ”<br>☰ ☰ ⇤ ⇥ &nbsp;&nbsp;T</div>
      <div class="col-edit"></div>
    </div>
    <div class="col" style="left:614px">
      <div class="col-head"><svg width="10" height="11" viewBox="0 0 10 11"><path d="M3 0h4v1H6v3l4 7H0l4-7V1H3z" fill="#2563eb"/></svg>Things To Try</div>
      <div class="col-tools">Normal &nbsp;&nbsp;&nbsp;⇕ &nbsp;&nbsp;&nbsp;<b>B</b> <i>I</i> <u>U</u> <s>S</s> ”<br>☰ ☰ ⇤ ⇥ &nbsp;&nbsp;T</div>
      <div class="col-edit"></div>
    </div>
  </div>
</div>

<!-- features -->
<section>
  <h2 class="abs section-title" style="top:926px">Features</h2>
  <div class="abs rule" style="left:570px;top:1005px;width:42px"></div>

  <div class="abs feature" style="left:115px">
    <div class="feature-icon"><svg width="48" height="48" viewBox="0 0 48 48" fill="none" stroke="#fff" stroke-width="2"><path d="M24 6l6 3.5v7L24 20l-6-3.5v-7z"/><path d="M12 20l6 3.5v7L12 34l-6-3.5v-7z"/><path d="M36 20l6 3.5v7L36 34l-6-3.5v-7z"/><path d="M24 30l6 3.5v7L24 44l-6-3.5v-7z"/><path d="M18 16l-3 5M30 16l3 5M18 29h12"/></svg></div>
    <h3>Structured Reflection</h3>
    <p>Lorem ipsum dolor sit amet, consectetur adipiscing elit, sed do eiusmod tempor incididunt ut labore et dolore magna aliqua. Ut enim ad minim veniam</p>
  </div>
  <div class="abs feature" style="left:358px">
    <div class="feature-icon"><svg width="48" height="48" viewBox="0 0 48 48" fill="none" stroke="#fff" stroke-width="2"><path d="M8 40h32"/><rect x="10" y="28" width="6" height="12"/><rect x="20" y="22" width="6" height="18"/><rect x="30" y="16" width="6" height="24"/><path d="M10 22L34 6M28 6h6v6"/></svg></div>
    <h3>Track Your Growth</h3>
    <p>Lorem ipsum dolor sit amet, consectetur adipiscing elit, sed do eiusmod tempor incididunt ut labore et dolore magna aliqua. Ut enim ad minim veniam</p>
  </div>
  <div class="abs feature" style="left:600px">
    <div class="feature-icon"><svg width="48" height="48" viewBox="0 0 48 48" fill="none" stroke="#fff" stroke-width="2"><rect x="6" y="8" width="36" height="30" rx="2"/><path d="M6 14h36M18 14v24M22 20h16M22 26h16M22 32h10M10 20h4M10 26h4"/></svg></div>
    <h3>User-Friendly Interface</h3>
    <p>Lorem ipsum dolor sit amet, consectetur adipiscing elit, sed do eiusmod tempor incididunt ut labore et dolore magna aliqua. Ut enim ad minim veniam</p>
  </div>
  <div class="abs feature" style="left:853px">
    <div class="feature-icon"><svg width="48" height="48" viewBox="0 0 48 48" fill="none" stroke="#fff" stroke-width="2"><path d="M14 32a8 8 0 010-16 11 11 0 0121-2 8 8 0 01-1 18"/><rect x="19" y="22" width="10" height="9" rx="1"/><path d="M21 22v-3a3 3 0 016 0v3M24 31v8M16 44h16"/></svg></div>
    <h3>Secure and Private</h3>
    <p>Lorem ipsum dolor sit amet, consectetur adipiscing elit, sed do eiusmod tempor incididunt ut labore et dolore magna aliqua. Ut enim ad minim veniam</p>
  </div>
</section>

<!-- row 1 -->
<section>
  <div class="abs shot" style="left:131px;top:1416px">
    <div class="shot-screen">
      <div class="app" style="transform:scale(.442)">
        <div class="app-side"><div class="side-logo"></div><div class="side-ico" style="top:46px"></div><div class="side-ico" style="top:67px"></div><div class="side-ico" style="top:88px"></div><div class="side-avatar"></div></div>
        <div class="app-title">Entry</div><div class="app-date">Wed Aug 21 2024 ⌄</div><div class="app-pill">Default Journal</div>
        <div class="col" style="left:101px;height:410px"><div class="col-head">What Went Well?</div><div class="col-tools">Normal ⇕ <b>B</b> <i>I</i> <u>U</u> <s>S</s></div><div class="col-edit"></div></div>
        <div class="col" style="left:357px;height:410px"><div class="col-head">What Didn't Go Well?</div><div class="col-tools">Normal ⇕ <b>B</b> <i>I</i> <u>U</u> <s>S</s></div><div class="col-edit"></div></div>
        <div class="col" style="left:614px;height:410px"><div class="col-head">Things To Try</div><div class="col-tools">Normal ⇕ <b>B</b> <i>I</i> <u>U</u> <s>S</s></div><div class="col-edit"></div></div>
      </div>
    </div>
  </div>
  <h2 class="abs row-title" style="left:643px;top:1418px">Lorem ipsum dolor sit<br>amet consectet</h2>
  <p class="abs row-text" style="left:644px;top:1524px">Sed ut perspiciatis unde omnis iste natus error sit voluptatem accusantium doloremque laudantium, totam rem aperiam, eaque ipsa quae ab illo inventore veritatis et quasi architecto beatae vitae dicta sunt explicabo. Nemo enim ipsam voluptatem quia voluptas sit aspernatur</p>
  <a class="abs btn row-btn" style="left:643px;top:1657px" href="#">Read More</a>
</section>

<!-- row 2 -->
<section>
  <h2 class="abs row-title" style="left:134px;top:1781px">Lorem ipsum dolor sit<br>amet consectet</h2>
  <p class="abs row-text" style="left:137px;top:1887px">Sed ut perspiciatis unde omnis iste natus error sit voluptatem accusantium doloremque laudantium, totam rem aperiam, eaque ipsa quae ab illo inventore veritatis et quasi architecto beatae vitae dicta sunt explicabo. Nemo enim ipsam voluptatem quia voluptas sit aspernatur</p>
  <a class="abs btn row-btn" style="left:135px;top:2020px" href="#">Read More</a>
  <div class="abs shot" style="left:618px;top:1779px">
    <div class="shot-screen">
      <div class="app" style="transform:scale(.442)">
        <div class="app-side"><div class="side-logo"></div><div class="side-ico" style="top:46px"></div><div class="side-ico" style="top:67px"></div><div class="side-ico" style="top:88px"></div><div class="side-avatar"></div></div>
        <div class="app-title">Entry</div><div class="app-date">Thu Aug 22 2024 ⌄</div><div class="app-pill" style="background:var(--green)">Saved</div>
        <div class="col" style="left:101px;height:410px"><div class="col-head">What Went Well?</div><div class="col-tools">Normal ⇕ <b>B</b> <i>I</i> <u>U</u> <s>S</s></div><div class="col-edit"><i></i><i style="width:70%"></i><i></i><i style="width:60%"></i><i></i><i style="width:50%"></i></div></div>
        <div class="col" style="left:357px;height:410px"><div class="col-head">What Didn't Go Well?</div><div class="col-tools">Normal ⇕ <b>B</b> <i>I</i> <u>U</u> <s>S</s></div><div class="col-edit"><i></i><i style="width:75%"></i><i></i><i style="width:55%"></i><i style="width:80%"></i></div></div>
        <div class="col" style="left:614px;height:410px"><div class="col-head">Things To Try</div><div class="col-tools">Normal ⇕ <b>B</b> <i>I</i> <u>U</u> <s>S</s></div><div class="col-edit"><i></i><i style="width:70%"></i><i></i><i></i><i style="width:60%"></i><i></i><i style="width:45%"></i></div></div>
      </div>
    </div>
  </div>
</section>

<!-- row 3: AI coach -->
<section>
  <div class="abs shot" style="left:131px;top:2151px">
    <div class="shot-screen">
      <div class="app" style="transform:scale(.442)">
        <div class="app-side"><div class="side-logo"></div><div class="side-ico" style="top:46px"></div><div class="side-ico" style="top:67px"></div><div class="side-ico" style="top:88px"></div><div class="side-avatar"></div></div>
        <div class="app-pill" style="left:90px;top:30px;background:#fff;color:var(--ink);border:1px solid var(--line)">+ Add New</div>
        <div class="app-pill" style="left:830px;top:26px;background:var(--green)">Sort</div>
        <div class="list-card" style="top:60px;height:240px"><b>Thu Aug 22 2024</b><i style="width:20%"></i><i style="width:40%"></i><i style="width:35%"></i><i style="width:45%"></i><i style="width:20%"></i><i style="width:55%"></i><i style="width:40%"></i><i style="width:45%"></i><i style="width:20%"></i><i style="width:60%"></i><i style="width:50%"></i><i style="width:45%"></i></div>
        <div class="list-card" style="top:320px;height:200px"><b>Tue Aug 20 2024</b><i style="width:20%"></i><i style="width:45%"></i><i style="width:40%"></i></div>
      </div>
    </div>
  </div>
  <h2 class="abs row-title" style="left:643px;top:2153px">Your AI coach is<br>coming soon</h2>
  <p class="abs row-text" style="left:644px;top:2259px">Soon an AI coach will read the history of your journal entries and offer gentle, personal insights: patterns in what went well, blockers that keep coming back, and fresh ideas worth trying next. Guidance that grows smarter with every reflection you write.</p>
  <a class="abs btn row-btn" style="left:643px;top:2391px" href="#">Read More</a>
</section>

<!-- testimonial -->
<section>
  <div class="abs band" style="top:2515px;height:420px"></div>
  <svg class="abs" style="left:576px;top:2580px" width="58" height="46" viewBox="0 0 58 46" fill="none" stroke="#0b4ea8" stroke-width="2.2"><path d="M24 4C12 8 3 18 3 30a12 12 0 1012-12c-2 0-3 .3-4 .6C13 12 18 8 24 6z"/><path d="M55 4C43 8 34 18 34 30a12 12 0 1012-12c-2 0-3 .3-4 .6C44 12 49 8 55 6z"/></svg>
  <p class="abs quote-text">Lorem ipsum dolor sit amet, consectetur adipiscing elit, sed do eiusmod tempor<br>incididunt ut labore et dolore magna aliqua. Ut enim ad minim veniam, quis<br>nostrud exercitation ullamco laboris nisi ut aliquip ex ea commodo consequat.<br>Duis aute irure dolor in reprehenderit in voluptate velit</p>
  <div class="abs arrow" style="left:100px;top:2709px"><svg width="14" height="20" viewBox="0 0 14 20" fill="none" stroke="#0b4ea8" stroke-width="2"><path d="M11 2L3 10l8 8"/></svg></div>
  <div class="abs arrow" style="left:1047px;top:2709px"><svg width="14" height="20" viewBox="0 0 14 20" fill="none" stroke="#0b4ea8" stroke-width="2"><path d="M3 2l8 8-8 8"/></svg></div>
  <div class="abs rule" style="left:572px;top:2823px;width:55px;background:#b9c6d6"></div>
  <div class="abs author">Mark Smith</div>
</section>

<!-- call to action -->
<section class="abs cta">
  <div class="cta-blob" style="left:120px;top:150px"></div>
  <div class="cta-blob" style="left:960px;top:120px"></div>
  <div class="cta-blob" style="left:700px;top:-330px;opacity:.6"></div>
  <h2 class="abs cta-title">Start Your Journey Today</h2>
  <p class="abs cta-text">Ready to take control of your personal growth? Begin your reflective<br>journey with our app and see the difference it makes.</p>
  <a class="abs cta-btn" href="#">Get Started for Free</a>
</section>

<!-- footer -->
<footer>
  <div class="abs brand foot-logo">Zestora</div>
  <nav class="abs foot-col" style="left:363px;top:3409px"><h4>Features</h4><a href="#">How It Works</a><a href="#">For Teams</a><a href="#">Pricing</a><a href="#">Templates</a></nav>
  <nav class="abs foot-col" style="left:553px;top:3409px"><h4>Menu</h4><a href="#">Home</a><a href="#">About Us</a><a href="#">Features</a><a href="#">Resources</a><a href="#">Pricing</a></nav>
  <nav class="abs foot-col" style="left:720px;top:3409px"><h4>Company</h4><a href="#">About Us</a><a href="#">Careers</a><a href="#">Press</a></nav>
  <div class="abs foot-col" style="left:895px;top:3409px"><h4>Follow us</h4>
    <div class="social"><span aria-label="Social profile 1"></span><span aria-label="Social profile 2"></span><span aria-label="Social profile 3"></span><span aria-label="Social profile 4"></span><span aria-label="Social profile 5"></span></div>
  </div>
  <div class="abs foot-rule"></div>
  <p class="abs legal">Terms &amp; Conditions &nbsp;| &nbsp;Privacy Policy &nbsp;&nbsp;| &nbsp;Copyright © 2024 All Rights Reserved</p>
</footer>

</body>
</html>
```